Website Design - TallyPorchHelpers.net

PLEASE CHECK WORD DOCUMENT ATTACHED FOR WEBSITE FLOW.

Target Market(s)

REAL ESTATE AGENTS ARE THE TARGET MARKET

Industry/Entity Type

Real Estate

Coding

Coded - Design and coding required

Number of Pages Required

4 page

Colors

Designer to choose colors to be used in the design.

Requirements
Must have
• WE LIKE RED LOGO ATTACHED
Nice to have
• PLEASE CHECK WORD DOCUMENT ATTACHED FOR WEBSITE FLOW.
Should not have

```html
<!DOCTYPE html>
<html lang="en">
<head>
<meta charset="utf-8">
<title>TallyPorchHelpers.net — Open House Sign Placement</title>
<link href="https://fonts.googleapis.com/css2?family=Montserrat:wght@400;500;600;700;800&family=Open+Sans:wght@400;600&family=Great+Vibes&display=swap" rel="stylesheet">
<style>
:root{
  --red:#e3232b;
  --red-dark:#c3161e;
  --navy:#23277a;
  --navy-dark:#181b5c;
  --purple:#4a2d8c;
  --plum:#9a2a5e;
  --ink:#2b2b35;
  --muted:#6b6b78;
  --line:#e3e3ea;
  --paper:#ffffff;
  --mist:#f3f3f5;
}
*{box-sizing:border-box;margin:0;padding:0}
html,body{width:1200px;height:4762px;overflow:hidden}
body{font-family:"Open Sans",Arial,sans-serif;color:var(--ink);background:var(--paper);font-size:13px;line-height:1.55}
h1,h2,h3,h4,.btn,.nav a{font-family:"Montserrat",Arial,sans-serif}
.wrap{width:736px;margin:0 auto;position:relative}
.btn{display:inline-block;background:var(--red);color:#fff;font-weight:700;font-size:12px;letter-spacing:.5px;text-transform:uppercase;padding:11px 26px;border-radius:3px;text-decoration:none;white-space:nowrap}
.btn-row{text-align:center}
.section-title{font-size:24px;font-weight:700;text-align:center;color:var(--ink)}

/* header */
.site-header{height:80px;background:#fff;display:flex;align-items:center}
.site-header .wrap{display:flex;align-items:center;justify-content:space-between}
.brand{display:flex;align-items:center;gap:7px;color:var(--red);font-family:"Montserrat",sans-serif;font-weight:800;font-size:13px;white-space:nowrap}
.brand-mark{width:20px;height:20px;background:var(--red);flex:0 0 20px}
.nav{display:flex;gap:16px}
.nav a{font-size:10px;font-weight:600;color:var(--ink);text-decoration:none;text-transform:uppercase;white-space:nowrap}
.call{display:flex;align-items:center;gap:7px;white-space:nowrap}
.call small{display:block;font-size:9px;color:var(--muted);line-height:1}
.call strong{font-family:"Montserrat",sans-serif;color:var(--red);font-size:14px;font-weight:700}

/* hero */
.hero{height:523px;position:relative;background:linear-gradient(180deg,#cfc7c0 0%,#b9aca4 45%,#8a7068 100%);display:flex;flex-direction:column;align-items:center;justify-content:center;text-align:center;color:#fff}
.hero::after{content:"";position:absolute;inset:0;background:rgba(30,20,25,.28)}
.hero > *{position:relative;z-index:1}
.hero h1{font-size:34px;font-weight:700;margin-top:30px}
.hero p{font-size:18px;font-weight:600;margin-top:6px;line-height:1.35}

/* choose */
.choose{height:238px;background:var(--red);padding-top:40px}
.choose h2{color:#fff;font-size:22px;font-weight:700;text-align:center}
.choose-cards{display:flex;justify-content:space-between;margin-top:26px}
.choose-card{width:226px;height:127px;background:#fff;border-bottom:8px solid var(--navy);box-shadow:0 4px 0 var(--red-dark);display:flex;flex-direction:column;align-items:center;justify-content:center;text-align:center;font-family:"Montserrat",sans-serif}
.choose-card svg{margin-bottom:8px}
.choose-card span{font-size:11px;font-weight:700;text-transform:uppercase;color:var(--ink);line-height:1.3}

/* how it works */
.how{height:518px;padding-top:46px}
.how h2{margin-top:70px}
.steps{display:flex;justify-content:space-between;align-items:flex-start;margin-top:40px}
.step{width:200px;text-align:center}
.step-num{width:44px;height:44px;border-radius:50%;background:var(--navy);color:#fff;font-family:"Montserrat",sans-serif;font-weight:700;font-size:12px;display:flex;align-items:center;justify-content:center;margin:0 auto 14px}
.step p{font-size:12px;color:var(--muted)}
.step-arrow{margin-top:16px;flex:0 0 50px}
.how .btn-row{margin-top:30px}

/* pricing */
.pricing{height:679px;background:var(--mist);padding-top:54px}
.plans{display:flex;justify-content:space-between;margin-top:28px}
.plan{flex:0 0 138px;width:138px;height:432px;background:#fff;box-shadow:0 2px 6px rgba(0,0,0,.08);text-align:center;position:relative}
.plan-head{height:38px;display:flex;align-items:center;justify-content:center;font-family:"Montserrat",sans-serif;font-weight:700;font-size:13px;color:var(--ink);border-bottom:1px solid var(--line)}
.plan-price{width:52px;height:52px;border-radius:50%;background:var(--red);color:#fff;font-family:"Montserrat",sans-serif;font-weight:800;font-size:16px;display:flex;align-items:center;justify-content:center;margin:10px auto 8px}
.plan.featured .plan-head{background:var(--red);color:#fff}
.plan.featured .plan-price{background:var(--navy)}
.plan ul{list-style:none;text-align:left;padding:0 14px}
.plan li{font-size:10px;color:var(--muted);padding-left:14px;position:relative;margin-bottom:12px;line-height:1.4}
.plan li::before{content:"";position:absolute;left:0;top:3px;width:7px;height:4px;border-left:2px solid var(--red);border-bottom:2px solid var(--red);transform:rotate(-45deg)}
.plan .btn{background:var(--navy);font-size:9px;padding:9px 0;width:104px;position:absolute;left:17px;bottom:48px;white-space:normal;line-height:1.3;letter-spacing:.2px}
.plan.featured .btn{background:var(--red)}
.plan small{position:absolute;left:12px;right:12px;bottom:14px;font-size:8px;color:var(--muted);line-height:1.3}
.plan.quote ul{margin-top:70px}
.pricing .btn-row{margin-top:40px}

/* marketing */
.marketing{height:613px;background:linear-gradient(100deg,var(--purple) 0%,#5a2c86 55%,var(--plum) 100%);color:#fff;padding-top:64px;position:relative}
.marketing h2{font-size:22px;font-weight:700}
.services{display:grid;grid-template-columns:220px 220px;column-gap:46px;row-gap:26px;margin-top:32px}
.service h3{font-size:13px;font-weight:700;display:flex;align-items:center;gap:10px;text-transform:uppercase}
.service-icon{width:30px;height:30px;border:2px solid #fff;border-radius:50%;display:flex;align-items:center;justify-content:center}
.service p{font-size:11px;opacity:.9;margin-top:8px;line-height:1.5}
.marketing .btn{margin-top:30px}
.agent-photo{position:absolute;right:120px;bottom:0;width:336px;height:490px;background:linear-gradient(180deg,#6a3b6a 0%,#b4485f 40%,#f1e6e6 55%,#d43a3c 75%,#3c2530 100%);border-radius:4px 4px 0 0;opacity:.92}

/* service area */
.area{height:159px;background:var(--navy);padding-top:42px;text-align:center;color:#fff}
.area h2{font-size:22px;font-weight:700}
.area-form{display:flex;justify-content:center;margin-top:16px}
.area-form input{width:380px;height:32px;border:0;padding:0 12px;font-size:11px;font-family:inherit}
.area-form button{width:96px;height:32px;border:0;background:var(--red);color:#fff;font-family:"Montserrat",sans-serif;font-weight:700;font-size:11px}
.map{height:419px;background:linear-gradient(135deg,#a9cde6 0%,#c8e0ee 35%,#ece7d6 60%,#e3dccb 100%)}
.map-cta{height:89px;display:flex;align-items:center;justify-content:center}

/* faq */
.faq{height:524px;background:linear-gradient(100deg,#4e2b88 0%,#7b2a72 55%,#b92a47 100%);padding-top:62px}
.faq h2{color:#fff}
.faq-cols{display:flex;justify-content:space-between;margin-top:32px}
.faq-col{width:356px}
.faq-item{background:#fff;height:32px;margin-bottom:10px;display:flex;align-items:center;justify-content:space-between;padding:0 12px;font-size:11px;font-weight:600;color:var(--ink)}
.faq-item::after{content:"+";color:var(--red);font-weight:700;font-size:14px}
.faq-item.open{background:var(--red);color:#fff;margin-bottom:0}
.faq-item.open::after{content:"−";color:#fff}
.faq-answer{background:#fff;padding:12px;font-size:10.5px;color:var(--muted);margin-bottom:10px;line-height:1.55}
.faq .btn-row{margin-top:60px}

/* testimonials */
.testimonials{height:565px;background:var(--mist);padding-top:58px}
.quotes{display:flex;justify-content:space-between;margin-top:34px}
.quote{width:340px;text-align:center;position:relative}
.quote-mark{position:absolute;top:-6px;font-family:"Montserrat",sans-serif;font-size:40px;font-weight:800;color:var(--red);line-height:1}
.quote-mark.l{left:-12px}.quote-mark.r{right:-12px}
.quote p{font-size:11.5px;color:var(--muted);padding:0 20px}
.avatar{width:50px;height:50px;border-radius:50%;background:linear-gradient(160deg,#c9b2a5,#7d6a62);margin:18px auto 8px;border:3px solid #fff;box-shadow:0 0 0 1px var(--line)}
.quote cite{font-family:"Great Vibes",cursive;font-style:normal;font-size:22px;color:var(--ink)}
.dots{display:flex;justify-content:center;gap:6px;margin-top:60px}
.dots i{width:8px;height:8px;border-radius:50%;background:#cfcfd6}
.dots i.on{background:var(--red)}
.testimonials .btn-row{margin-top:56px}

/* newsletter */
.newsletter{height:23px;position:relative;border-top:4px solid var(--red);background:var(--navy)}
.newsletter .ribbon{position:absolute;left:50%;top:-18px;transform:translateX(-50%);width:300px;height:32px;background:var(--red);color:#fff;font-family:"Montserrat",sans-serif;font-weight:700;font-size:11px;text-transform:uppercase;display:flex;align-items:center;justify-content:center;gap:8px;clip-path:polygon(0 0,100% 0,94% 100%,6% 100%)}

/* footer */
.site-footer{height:295px;background:var(--navy);color:#d9dbf2;padding-top:26px}
.footer-cols{display:flex;justify-content:space-between}
.footer-col h4{font-size:11px;font-weight:700;color:#fff;text-transform:uppercase;margin-bottom:10px}
.footer-col p,.footer-col li{font-size:10px;line-height:1.7}
.footer-col ul{list-style:none}
.col-about{width:200px}.col-contact{width:160px}.col-links{width:100px}.col-form{width:170px}
.social{display:flex;gap:6px;margin-top:10px}
.social i{width:20px;height:20px;border-radius:50%;border:1.5px solid #fff}
.footer-form input{display:block;width:100%;height:22px;border:0;margin-bottom:6px;padding:0 8px;font-size:9px;font-family:inherit}
.footer-form button{width:100%;height:24px;border:0;background:var(--red);color:#fff;font-family:"Montserrat",sans-serif;font-weight:700;font-size:9px;text-transform:uppercase}
.footer-bar{height:37px;background:var(--navy-dark);color:#b9bcdc;font-size:10px}
.footer-bar .wrap{display:flex;justify-content:space-between;align-items:center;height:37px}
</style>
</head>
<body>

<header class="site-header">
  <div class="wrap">
    <div class="brand"><span class="brand-mark"></span>TallyPorchHelpers.net</div>
    <nav class="nav">
      <a href="#how">How It Works</a><a href="#area">Service Area</a><a href="#pricing">Pricing</a><a href="#about">About Us</a><a href="#faq">FAQ</a>
    </nav>
    <div class="call">
      <svg width="16" height="16" viewBox="0 0 24 24"><path fill="#e3232b" d="M6.6 10.8a15 15 0 006.6 6.6l2.2-2.2a1 1 0 011-.25 11.4 11.4 0 003.6.57 1 1 0 011 1V20a1 1 0 01-1 1A17 17 0 013 4a1 1 0 011-1h3.5a1 1 0 011 1c0 1.25.2 2.45.57 3.6a1 1 0 01-.25 1z"/></svg>
      <div><small>Call Us Now</small><strong>1-415-555-0162</strong></div>
    </div>
  </div>
</header>

<section class="hero" role="img" aria-label="Photo of a couple walking through the open doors of a bright house">
  <h1>Helping agents save time and money.</h1>
  <p>We place signs and boost foot traffic to your open houses<br>using proven marketing techniques.</p>
</section>

<section class="choose">
  <div class="wrap">
    <h2>Choose The Option Below That Best Describes You</h2>
    <div class="choose-cards">
      <div class="choose-card">
        <svg width="30" height="26" viewBox="0 0 30 26"><rect x="3" y="4" width="24" height="20" fill="none" stroke="#e3232b" stroke-width="2"/><path d="M8 9h3M14 9h3M20 9h3M8 14h3M14 14h3M20 14h3M13 24v-5h4v5" stroke="#e3232b" stroke-width="2"/></svg>
        <span>I'm a<br>Full On Brokerage</span>
      </div>
      <div class="choose-card">
        <svg width="32" height="26" viewBox="0 0 32 26"><circle cx="16" cy="7" r="5" fill="#e3232b"/><circle cx="6" cy="10" r="3.5" fill="#e3232b"/><circle cx="26" cy="10" r="3.5" fill="#e3232b"/><path d="M7 25a9 9 0 0118 0zM0 25a6 6 0 0110-4v4zM32 25a6 6 0 00-10-4v4z" fill="#e3232b"/></svg>
        <span>I'm an<br>Ind. Broker With A Team</span>
      </div>
      <div class="choose-card">
        <svg width="28" height="28" viewBox="0 0 28 28"><path d="M5 2v26M5 5h20" stroke="#e3232b" stroke-width="2.5"/><rect x="8" y="8" width="16" height="11" fill="#e3232b"/></svg>
        <span>I Need<br>Sign Placement ASAP</span>
      </div>
    </div>
  </div>
</section>

<section class="how" id="how">
  <div class="wrap">
    <div class="btn-row"><a class="btn" href="#contact">Contact Us Right Now</a></div>
    <h2 class="section-title">How It Works</h2>
    <div class="steps">
      <div class="step"><div class="step-num">01</div><p>We boost foot traffic to your open house using proven marketing channels, social media ads, SMS notifications, voice broadcasts and email notifications</p></div>
      <svg class="step-arrow" width="50" height="12" viewBox="0 0 50 12"><path d="M0 6h46M40 1l6 5-6 5" stroke="#9a9aa6" stroke-width="1.5" fill="none"/></svg>
      <div class="step"><div class="step-num">02</div><p>We place open house signs strategically in the surrounding area</p></div>
      <svg class="step-arrow" width="50" height="12" viewBox="0 0 50 12"><path d="M0 6h46M40 1l6 5-6 5" stroke="#9a9aa6" stroke-width="1.5" fill="none"/></svg>
      <div class="step"><div class="step-num">03</div><p>Store custom signs for you if needed</p></div>
    </div>
    <div class="btn-row"><a class="btn" href="#contact">Contact Us Right Now</a></div>
  </div>
</section>

<section class="pricing" id="pricing">
  <div class="wrap">
    <h2 class="section-title">Choose Your Package</h2>
    <div class="plans">
      <div class="plan"><div class="plan-head">5 SIGNS</div><div class="plan-price">$49</div>
        <ul><li>Place signs strategically in best areas according to where the open house is located</li><li>Pick up the signs after the open house</li><li>Store custom signs for you if needed</li></ul>
        <a class="btn" href="#signup">Sign Up</a><small>Starting at 5 signs per open house, billed monthly</small></div>
      <div class="plan"><div class="plan-head">10 SIGNS</div><div class="plan-price">$59</div>
        <ul><li>Place signs strategically in best areas according to where the open house is located</li><li>Pick up the signs after the open house</li><li>Store custom signs for you if needed</li></ul>
        <a class="btn" href="#signup">Sign Up</a><small>Starting at 10 signs per open house, billed monthly</small></div>
      <div class="plan featured"><div class="plan-head">15 SIGNS</div><div class="plan-price">$69</div>
        <ul><li>Place signs strategically in best areas according to where the open house is located</li><li>Pick up the signs after the open house</li><li>Store custom signs for you if needed</li></ul>
        <a class="btn" href="#signup">Sign Up</a><small>Starting at 15 signs per open house, billed monthly</small></div>
      <div class="plan"><div class="plan-head">20 SIGNS</div><div class="plan-price">$79</div>
        <ul><li>Place signs strategically in best areas according to where the open house is located</li><li>Pick up the signs after the open house</li><li>Store custom signs for you if needed</li></ul>
        <a class="btn" href="#signup">Sign Up</a><small>Starting at 20 signs per open house, billed monthly</small></div>
      <div class="plan quote"><div class="plan-head">25+ SIGNS</div>
        <ul><li>Place signs strategically in best areas according to where the open house is located</li><li>Pick up the signs after the open house</li><li>Store custom signs for you if needed</li></ul>
        <a class="btn" href="#quote">Click Here To Create A Quote</a><small>Larger packages priced per open house, quoted on request</small></div>
    </div>
    <div class="btn-row"><a class="btn" href="#contact">Contact Us Right Now</a></div>
  </div>
</section>

<section class="marketing">
  <div class="wrap">
    <h2>Marketing Services</h2>
    <div class="services">
      <div class="service"><h3><span class="service-icon"><svg width="14" height="12" viewBox="0 0 14 12"><path d="M1 1h12v8H5l-3 2V9H1z" fill="none" stroke="#fff" stroke-width="1.4"/></svg></span>SMS</h3>
        <p>We will send a text message to all the people that live in the surrounding area of your open house to let them know there is a home for sale nearby and invite them to come check it out.</p></div>
      <div class="service"><h3><span class="service-icon"><svg width="14" height="11" viewBox="0 0 14 11"><rect x="1" y="1" width="12" height="9" fill="none" stroke="#fff" stroke-width="1.4"/><path d="M1 1l6 5 6-5" fill="none" stroke="#fff" stroke-width="1.4"/></svg></span>Email</h3>
        <p>We will send an email message to all the people that live in the surrounding area of your open house to let them know there is a home for sale nearby and invite them to come check it out.</p></div>
      <div class="service"><h3><span class="service-icon"><svg width="12" height="12" viewBox="0 0 12 12"><rect x="1" y="1" width="10" height="10" fill="none" stroke="#fff" stroke-width="1.4"/></svg></span>Social Ads</h3>
        <p>We will place a social ad in front of the home buyers of all the people that live in the surrounding area of your open house to let them know there is a home for sale nearby and invite them to come check it out.</p></div>
      <div class="service"><h3><span class="service-icon"><svg width="10" height="14" viewBox="0 0 10 14"><rect x="2.5" y="1" width="5" height="8" rx="2.5" fill="none" stroke="#fff" stroke-width="1.4"/><path d="M1 7a4 4 0 008 0M5 11v2" fill="none" stroke="#fff" stroke-width="1.4"/></svg></span>Voice Broadcast</h3>
        <p>We will send a voice broadcast to all the people that live in the surrounding area of your open house to let them know there is a home for sale nearby and invite them to come check it out.</p></div>
    </div>
    <a class="btn" href="#contact">Contact Us Right Now</a>
  </div>
  <div class="agent-photo" role="img" aria-label="Photo of a smiling real estate agent holding a red SOLD sign"></div>
</section>

<section class="area" id="area">
  <h2>Service Area</h2>
  <form class="area-form"><input type="text" placeholder="Enter Your Open House Address"><button type="button">SUBMIT</button></form>
</section>
<div class="map" role="img" aria-label="Map of the coastal service region with covered neighborhoods"></div>
<div class="map-cta"><a class="btn" href="#contact">Contact Us Right Now</a></div>

<section class="faq" id="faq">
  <div class="wrap">
    <h2 class="section-title">Frequently Asked Questions</h2>
    <div class="faq-cols">
      <div class="faq-col">
        <div class="faq-item">How soon can signs be placed near my listing?</div>
        <div class="faq-item">Do you pick up the signs after the open house?</div>
        <div class="faq-item">Can you store my own branded signs for me?</div>
        <div class="faq-item">Which neighborhoods do you currently cover?</div>
      </div>
      <div class="faq-col">
        <div class="faq-item">How are the marketing messages targeted?</div>
        <div class="faq-item open">What is included in every sign package?</div>
        <div class="faq-answer">Every package covers placing your signs at the best corners around the listing, collecting them once the open house ends, and storing custom signs between events so they are ready whenever you need them next time.</div>
        <div class="faq-item">Can I change my package from month to month?</div>
        <div class="faq-item">How do I book my first open house?</div>
      </div>
    </div>
    <div class="btn-row"><a class="btn" href="#contact">Contact Us Right Now</a></div>
  </div>
</section>

<section class="testimonials">
  <div class="wrap">
    <h2 class="section-title">Clients Testimonials</h2>
    <div class="quotes">
      <div class="quote"><span class="quote-mark l">“</span>
        <p>Our open houses used to be quiet afternoons. Since the team started placing signs and sending neighborhood messages, we see steady foot traffic from the first hour, and I no longer spend my morning driving signs around town before every showing.</p>
        <div class="avatar" role="img" aria-label="Client portrait"></div><cite>Marla Keene</cite></div>
      <div class="quote"><span class="quote-mark r">”</span>
        <p>Booking is simple and the signs are always up on time. The text and email outreach brought in buyers who lived just a few streets away, and two of them made offers within a week. It has saved our team hours of work every weekend.</p>
        <div class="avatar" role="img" aria-label="Client portrait"></div><cite>Walter Dunn</cite></div>
    </div>
    <div class="dots"><i></i><i class="on"></i><i></i><i></i></div>
    <div class="btn-row"><a class="btn" href="#contact">Contact Us Right Now</a></div>
  </div>
</section>

<div class="newsletter"><div class="ribbon"><svg width="14" height="11" viewBox="0 0 14 11"><rect x="1" y="1" width="12" height="9" fill="none" stroke="#fff" stroke-width="1.4"/><path d="M1 1l6 5 6-5" fill="none" stroke="#fff" stroke-width="1.4"/></svg>Subscribe To Our Newsletter</div></div>

<footer class="site-footer" id="about">
  <div class="wrap">
    <div class="footer-cols">
      <div class="footer-col col-about"><h4>About TallyPorchHelpers.net</h4>
        <p>TallyPorchHelpers.net was founded by agents who know how much time open house prep takes. We place signs, market to nearby neighbors and help you meet more buyers at every event.</p>
        <div class="social"><i></i><i></i><i></i><i></i><i></i></div></div>
      <div class="footer-col col-contact"><h4>Contact Information</h4>
        <p>2210 Larkview Road, Suite 40<br>Brookmere, CA 90000</p>
        <p style="color:#fff;font-weight:600;margin-top:6px">1-415-555-0162</p>
        <p>Mon–Sat 8am – 6pm</p>
        <p>hello@tallyporchhelpers.net</p></div>
      <div class="footer-col col-links"><h4>Quick Links</h4>
        <ul><li>How It Works</li><li>Service Area</li><li>Pricing</li><li>About Us</li><li>FAQ</li></ul></div>
      <div class="footer-col col-form" id="contact"><h4>Contact Us Right Now</h4>
        <form class="footer-form"><input placeholder="Name"><input placeholder="Email"><input placeholder="Phone"><input placeholder="Message"><button type="button">Send A Message</button></form></div>
    </div>
  </div>
</footer>
<div class="footer-bar"><div class="wrap"><span>Copyright © 2024 TallyPorchHelpers.net</span><span>Terms of Use | Privacy | Sitemap</span></div></div>

</body>
</html>
```